Harbourline Electrical Solutions

On one side. LOGO (underneath:) Commercial Industrial Residential

- NAME & CONTACT DETAILS

Marcus T. Hollings
Project Manager

(Cell icon) (441) 555-0187
(Email icon) hlelectricalsolutions@mailvento.com
(Facebook & Instagram icons )@hlelectricalsolutions

Other side: LOGO - underneath ELECTRICAL CONSTRUCTION & MAINTENANCE . LED LIGHTING & AUTOMATION . LIFE SAFETY SYSTEMS (FIRE ALARM / SECURITY) . DATA & COMMUNICATION

```html
<!DOCTYPE html>
<html lang="en">
<head>
<meta charset="utf-8">
<title>Harbourline Electrical Solutions – Business Card</title>
<link rel="stylesheet" href="https://fonts.googleapis.com/css2?family=Montserrat:wght@400;500;600;700&display=swap">
<style>
  :root {
    --backdrop: #262628;
    --teal: #10566b;
    --teal-dark: #0f5168;
    --white: #ffffff;
    --ink: #222326;
    --ink-soft: #3a3b3e;
  }
  * { box-sizing: border-box; margin: 0; padding: 0; }
  html, body {
    width: 1200px; height: 1200px; overflow: hidden;
    background: var(--backdrop);
    font-family: "Montserrat", sans-serif;
  }
  .canvas { position: relative; width: 1200px; height: 1200px; }

  .card { position: absolute; overflow: hidden; }

  /* Services side */
  .card--services {
    left: 292px; top: 220px; width: 599px; height: 359px;
    background: var(--teal);
  }
  .service-list {
    position: absolute; left: 48px; top: 146px;
    list-style: none; color: var(--white);
    font-weight: 500; font-size: 11px; line-height: 18px;
  }
  .service-list li::before {
    content: "•"; display: inline-block; width: 10px; font-size: 11px;
  }
  .brand-vertical {
    position: absolute; left: 475px; top: 334px;
    transform: rotate(-90deg); transform-origin: left top;
    width: 300px;
    color: var(--white); font-weight: 500;
    font-size: 16px; line-height: 18px; letter-spacing: 2.6px;
    text-transform: uppercase;
  }

  /* Contact side */
  .card--contact {
    left: 287px; top: 630px; width: 609px; height: 365px;
    background: var(--white);
  }
  .brand-block {
    position: absolute; left: 284px; top: 30px; width: 276px;
    display: flex; align-items: center; gap: 10px;
  }
  .brand-mark {
    width: 14px; height: 14px; background: var(--teal); flex: none;
  }
  .brand-name {
    color: var(--teal); font-weight: 500;
    font-size: 17px; line-height: 19px; letter-spacing: 2.2px;
    text-transform: uppercase;
  }
  .sector-line {
    position: absolute; left: 284px; top: 111px; width: 280px;
    font-size: 9.6px; font-weight: 500; letter-spacing: 2.4px;
    color: var(--ink); white-space: nowrap;
  }
  .sector-line .divider { color: var(--teal); padding: 0 3px; }

  .person { position: absolute; left: 46px; top: 243px; }
  .person-name {
    color: var(--teal-dark); font-weight: 700; font-size: 17px; line-height: 20px;
    text-transform: uppercase;
  }
  .person-role { color: var(--ink-soft); font-size: 12px; line-height: 16px; }
  .person-rule {
    position: absolute; left: 46px; top: 287px; width: 49px; height: 2px;
    background: var(--teal);
  }
  .contact-row {
    position: absolute; display: flex; align-items: center; gap: 4px;
    font-size: 12.5px; color: var(--ink); white-space: nowrap;
  }
  .contact-row svg { width: 13px; height: 13px; flex: none; }
  .contact-row--phone { left: 45px; top: 299px; }
  .contact-row--email { left: 45px; top: 318px; }
  .contact-row--social { left: 379px; top: 318px; gap: 6px; }
  .social-dot {
    width: 12px; height: 12px; border: 1.3px solid var(--teal); border-radius: 50%;
  }
</style>
</head>
<body>
<main class="canvas">

  <section class="card card--services" aria-label="Services side">
    <ul class="service-list">
      <li>ELECTRICAL CONSTRUCTION &amp; MAINTENANCE</li>
      <li>LED LIGHTING &amp; AUTOMATION</li>
      <li>LIFE SAFETY SYSTEMS (FIRE ALARM / SECURITY)</li>
      <li>DATA &amp; COMMUNICATION</li>
    </ul>
    <div class="brand-vertical">Harbourline<br>Electrical<br>Solutions</div>
  </section>

  <section class="card card--contact" aria-label="Contact side">
    <div class="brand-block">
      <span class="brand-mark"></span>
      <div class="brand-name">Harbourline<br>Electrical<br>Solutions</div>
    </div>
    <p class="sector-line">COMMERCIAL<span class="divider">|</span>INDUSTRIAL<span class="divider">|</span>RESIDENTIAL</p>

    <div class="person">
      <p class="person-name">Marcus T. Hollings</p>
      <p class="person-role">Project Manager</p>
    </div>
    <div class="person-rule"></div>

    <p class="contact-row contact-row--phone">
      <svg viewBox="0 0 14 14" aria-hidden="true"><circle cx="7" cy="7" r="6.2" fill="none" stroke="#10566b" stroke-width="1"/><path d="M4.6 4c.4-.4.8-.3 1 .1l.5 1c.1.3 0 .5-.2.7l-.3.3c.3.7.9 1.3 1.6 1.6l.3-.3c.2-.2.4-.3.7-.2l1 .5c.4.2.5.6.1 1-.6.6-1.3.8-2.2.4A5.5 5.5 0 0 1 4.2 6.2c-.4-.9-.2-1.6.4-2.2z" fill="#10566b"/></svg>
      (441) 555-0187
    </p>
    <p class="contact-row contact-row--email">
      <svg viewBox="0 0 14 14" aria-hidden="true"><circle cx="7" cy="7" r="6.2" fill="none" stroke="#10566b" stroke-width="1"/><rect x="4" y="4.8" width="6" height="4.4" fill="none" stroke="#10566b" stroke-width="0.9"/><path d="M4 4.8l3 2.4 3-2.4" fill="none" stroke="#10566b" stroke-width="0.9"/></svg>
      hlelectricalsolutions@mailvento.com
    </p>
    <p class="contact-row contact-row--social">
      <span class="social-dot"></span>
      @hlelectricalsolutions
    </p>
  </section>

</main>
</body>
</html>
```